Clearvale glass & hardware manufacturer

Need a SEO friendly, modern & professional looking website. We are selling all kinds of glass & accessories ( Glass/ Mirror/ splash back/ pool fence/ balustrade/ hardware...we are specialised on some special glass, like curve glass,tinted glass thermal & accoustic glass...) It should has simple & crisp feeling like a glass. It must be fully functional with product display and online ordering. Please see attached confirmed logo design(Blue & white). Make sure the theme color match its feel.

Target Market(s)

Architect and designer, Builder, & Developer

Industry/Entity Type

Manufacturer

Coding

Coded - Design and coding required

Font styles to use
Serif
Sans Serif

Colors

Designer to choose colors to be used in the design.

Requirements
Must have
• Glass & hardware theme and our logo
• Here are some competitor's website for reference. (Borrow ideas but not copy : )
• 1.https://www.tarvino.com.au/about
• 2.http://www.plumeretail.com.au/
• 3.http://www.kwd.com.au/
• 4.http://www.brackenhillfittings.com.au/
Nice to have
• Some transparent or semi transparent effects to make the website like a glass
Should not have
• No limitation for your imagination

```html
<!DOCTYPE html>
<html lang="en">
<head>
<meta charset="utf-8">
<title>Clearvale Glass & Hardware</title>
<link href="https://fonts.googleapis.com/css2?family=Open+Sans:wght@400;600&family=Roboto+Condensed:wght@400;700&display=swap" rel="stylesheet">
<style>
:root{
  --blue:#1f6fbf;
  --blue-dark:#14569b;
  --sky:#2b9ad8;
  --ink:#1d1d1d;
  --text:#555;
  --muted:#777;
  --soft:#f2f2f2;
  --footer-top:#1f1f1f;
  --footer-bottom:#0d0d0d;
}
*{box-sizing:border-box;margin:0;padding:0}
html,body{width:1200px;height:3136px;overflow:hidden}
body{position:relative;background:#fff;font-family:'Open Sans',Arial,sans-serif;color:var(--text)}
.abs{position:absolute}
.cond{font-family:'Roboto Condensed','Arial Narrow',sans-serif}

.topbar{left:0;top:0;width:1200px;height:38px;background:var(--sky);color:#fff;font-size:14px}
.topbar .contact{left:88px;top:9px;display:flex;gap:26px;align-items:center}
.topbar .contact span{display:flex;align-items:center;gap:8px}
.topbar .social{right:86px;top:10px;display:flex;gap:6px}
.topbar .social i{display:block;width:16px;height:16px;background:#fff;border-radius:2px;opacity:.95}

.header{left:0;top:38px;width:1200px;height:102px;background:#fff}
.brand{left:88px;top:35px;display:flex;align-items:center;gap:12px}
.brand .mark{width:30px;height:30px;background:var(--blue);border-radius:4px}
.brand .name{font-family:'Roboto Condensed',sans-serif;font-weight:700;font-size:28px;color:var(--blue);letter-spacing:1px}
.nav{top:36px;font-size:18px;color:#333}
.nav.active{color:var(--sky)}

.hero{left:0;top:140px;width:1200px;height:518px;background:linear-gradient(100deg,#cfd6da 0%,#eef0f0 35%,#e2e4e3 65%,#b99a7a 100%)}
.hero-card{left:579px;top:320px;width:532px;height:200px;background:rgba(255,255,255,.72);text-align:center}
.hero-card h1{font-family:'Roboto Condensed',sans-serif;font-weight:400;font-size:34px;color:#222;margin-top:30px}
.hero-card p{font-family:'Roboto Condensed',sans-serif;font-size:26px;color:#333;margin-top:4px}
.btn{display:inline-block;background:var(--blue-dark);color:#fff;border-radius:22px;font-size:17px;font-weight:600}
.hero-card .btn{margin-top:14px;padding:7px 22px;font-family:'Roboto Condensed',sans-serif;letter-spacing:.5px}
.arrow{width:28px;height:28px;border-radius:50%;background:rgba(40,40,40,.75)}

.section-title{left:0;width:1200px;text-align:center;font-family:'Roboto Condensed',sans-serif;font-size:38px;color:#1a1a1a}
.intro{left:130px;top:818px;width:940px;text-align:center;font-size:15.5px;line-height:28px}

.feature{top:975px;width:300px;text-align:center}
.feature h3{font-family:'Open Sans',sans-serif;font-weight:400;font-size:21px;color:#222;margin-top:22px}
.feature p{font-size:15px;line-height:22px;margin-top:10px}

.accessories{left:0;top:1233px;width:1200px;height:512px;background:linear-gradient(180deg,#3f6a94 0%,#5d86ab 45%,#33628f 100%)}
.card{top:1400px;width:242px;height:251px;background:rgba(230,236,242,.92);padding:10px}
.card .img{width:222px;height:184px}
.card span{display:block;text-align:center;font-size:20px;color:#222;margin-top:14px}

.whatwedo{left:109px;top:1837px;width:978px;height:333px;background:#fff;box-shadow:0 4px 18px rgba(0,0,0,.2)}
.whatwedo h2{left:58px;top:52px;font-family:'Roboto Condensed',sans-serif;font-weight:400;font-size:36px;color:#1a1a1a}
.whatwedo p{left:58px;top:114px;width:410px;text-align:justify;font-size:14.5px;line-height:26px}
.whatwedo .btn{left:60px;top:254px;padding:6px 20px;font-size:14px}
.video{left:520px;top:0;width:458px;height:333px;background:linear-gradient(160deg,#5c6870,#2f3a44 60%,#6b6250)}

.blog{left:0;top:2293px;width:1200px;height:533px;background:var(--soft)}
.post{top:2439px;width:312px}
.post .img{width:312px;height:174px}
.post .meta{margin-top:14px;display:flex;height:22px;font-size:13px;color:#fff}
.post .meta b{font-weight:400;background:var(--blue);padding:2px 14px}
.post .meta i{font-style:normal;background:#222;padding:2px 10px}
.post h4{font-weight:400;font-size:16px;color:#222;margin-top:12px}
.post p{font-size:13px;line-height:19px;color:var(--muted);margin-top:6px}
.post a{display:block;font-size:13px;color:var(--blue);margin-top:6px;text-decoration:none}

.footer{left:0;top:2826px;width:1200px;height:310px;background:linear-gradient(180deg,var(--footer-top),var(--footer-bottom));color:#ddd}
.footer .brand{left:94px;top:120px}
.footer .brand .name{color:#5fa8e6}
.footer .brand .mark{background:#5fa8e6}
.fcol{top:70px;font-size:12.5px;line-height:23px}
.fcol h5{font-weight:400;font-size:14px;color:#fff;margin-bottom:10px;letter-spacing:.3px}
.fsocial{display:flex;gap:14px;margin-top:14px}
.fsocial i{display:block;width:25px;height:25px;background:#eee;border-radius:3px}
.rule{left:94px;top:221px;width:1012px;height:1px;background:#333}
.copy{left:0;top:256px;width:1200px;text-align:center;font-size:12.5px}
</style>
</head>
<body>

<div class="abs topbar">
  <div class="abs contact">
    <span><svg width="12" height="12" viewBox="0 0 12 12"><rect width="12" height="12" rx="2" fill="#fff"/><path d="M3 3l2 0 1 2-1 1a5 5 0 002 2l1-1 2 1v2a7 7 0 01-7-7z" fill="#2b9ad8"/></svg>: (555) 214 - 7730</span>
    <span><svg width="13" height="10" viewBox="0 0 13 10"><rect width="13" height="10" rx="1" fill="#fff"/><path d="M0 0l6.5 5L13 0" stroke="#2b9ad8" fill="none"/></svg>: info@clearvale-glass.com</span>
  </div>
  <div class="abs social"><i></i><i></i><i></i><i></i></div>
</div>

<div class="abs header">
  <div class="abs brand"><div class="mark"></div><div class="name">CLEARVALE</div></div>
  <div class="abs nav active" style="left:489px">Home</div>
  <div class="abs nav" style="left:594px">About us</div>
  <div class="abs nav" style="left:721px">Services</div>
  <div class="abs nav" style="left:836px">Products</div>
  <div class="abs nav" style="left:959px">Blog</div>
  <div class="abs nav" style="left:1045px">Contact</div>
</div>

<div class="abs hero" role="img" aria-label="Bright office with frameless glass partition walls"></div>
<svg class="abs arrow" style="left:51px;top:394px" viewBox="0 0 28 28"><circle cx="14" cy="14" r="14" fill="#333" opacity=".8"/><path d="M16 9l-5 5 5 5" stroke="#fff" stroke-width="2.5" fill="none"/></svg>
<svg class="abs arrow" style="left:1120px;top:394px" viewBox="0 0 28 28"><circle cx="14" cy="14" r="14" fill="#333" opacity=".8"/><path d="M12 9l5 5-5 5" stroke="#fff" stroke-width="2.5" fill="none"/></svg>
<div class="abs hero-card">
  <h1>CLEARVALE GLASS &amp; HARDWARES</h1>
  <p>Selling all kinds of glass &amp; accessories</p>
  <span class="btn">BUY NOW</span>
</div>

<h2 class="abs section-title" style="top:756px">Welcome to Clearvale Glass &amp; Hardwares</h2>
<p class="abs intro">It is a long established fact that a reader will be distracted by the readable content of a page when looking at its layout. The point of using Lorem Ipsum is that it has a more-or-less normal distribution of letters, as opposed to using 'Content here, content here', making it look like readable English. Many desktop publishing packages and web page editors now use Lorem Ipsum.</p>

<div class="abs feature" style="left:118px">
  <svg width="56" height="48" viewBox="0 0 56 48"><g fill="#2b9ad8"><path d="M28 2l12 6-12 6-12-6z"/><path d="M16 10l11 5.5v12L16 22z"/><path d="M40 10l-11 5.5v12L40 22z"/><path d="M15 26l11 5.5-11 5.5-11-5.5z"/><path d="M41 26l11 5.5-11 5.5-11-5.5z"/><path d="M4 33l10 5v9L4 42z"/><path d="M52 33l-10 5v9l10-5z"/></g></svg>
  <h3>Our Products</h3>
  <p>It has survived not only five centuries,<br>but also the leap into electronic</p>
</div>
<div class="abs feature" style="left:450px">
  <svg width="56" height="48" viewBox="0 0 56 48"><rect x="12" y="10" width="32" height="22" rx="2" fill="none" stroke="#2b9ad8" stroke-width="3"/><path d="M6 36h44l-3 4H9z" fill="#2b9ad8"/></svg>
  <h3>Online Ordering</h3>
  <p>It has survived not only five centuries,<br>but also the leap into electronic</p>
</div>
<div class="abs feature" style="left:774px">
  <svg width="56" height="48" viewBox="0 0 56 48"><rect x="10" y="10" width="36" height="28" rx="2" fill="#2b9ad8"/><path d="M10 12l18 13 18-13" stroke="#fff" stroke-width="2.5" fill="none"/></svg>
  <h3>Contact Us</h3>
  <p>It has survived not only five centuries,<br>but also the leap into electronic</p>
</div>

<div class="abs accessories" role="img" aria-label="Modern glass-walled office interior in blue tones"></div>
<h2 class="abs section-title" style="top:1302px;color:#fff;font-size:34px">Glass &amp; Accessories</h2>
<svg class="abs" style="left:34px;top:1504px" width="30" height="30" viewBox="0 0 30 30"><circle cx="15" cy="15" r="14" fill="#fff" opacity=".35"/><path d="M17 9l-6 6 6 6" stroke="#fff" stroke-width="2.5" fill="none"/></svg>
<svg class="abs" style="left:1136px;top:1504px" width="30" height="30" viewBox="0 0 30 30"><circle cx="15" cy="15" r="14" fill="#fff" opacity=".35"/><path d="M13 9l6 6-6 6" stroke="#fff" stroke-width="2.5" fill="none"/></svg>
<div class="abs card" style="left:90px"><div class="img" role="img" aria-label="Frameless glass shower doors" style="background:linear-gradient(160deg,#a9d3cc,#6fa8a0)"></div><span>Glass</span></div>
<div class="abs card" style="left:349px"><div class="img" role="img" aria-label="Framed wall mirror" style="background:linear-gradient(160deg,#b7a8b0,#6f6068)"></div><span>Mirror</span></div>
<div class="abs card" style="left:610px"><div class="img" role="img" aria-label="Timber staircase with glass balustrade" style="background:linear-gradient(160deg,#e8e4e0,#9a4a2c)"></div><span>Balustrade</span></div>
<div class="abs card" style="left:870px"><div class="img" role="img" aria-label="Swimming pool with glass pool fence" style="background:linear-gradient(180deg,#5a7a45,#4fb3d6)"></div><span>Pool fence</span></div>

<div class="abs whatwedo">
  <h2 class="abs">What We Do</h2>
  <p class="abs">It is a long established fact that a reader will be distracted by the readable content of a page when looking at its layout. The point of using Lorem Ipsum is that it has a more-or-less normal distribution of letters, as opposed to using 'Content here, content here', making it look like readable English.</p>
  <span class="abs btn">Read More</span>
  <div class="abs video" role="img" aria-label="Video still of a curved glass balustrade along a walkway"></div>
  <svg class="abs" style="left:726px;top:142px" width="48" height="48" viewBox="0 0 48 48"><circle cx="24" cy="24" r="23" fill="#fff" opacity=".85"/><path d="M19 14l14 10-14 10z" fill="#333"/></svg>
</div>

<div class="abs blog"></div>
<h2 class="abs section-title" style="top:2342px">Latest Blog</h2>
<div class="abs post" style="left:96px">
  <div class="img" role="img" aria-label="Balcony with glass balustrade under blue sky" style="background:linear-gradient(160deg,#3a6fb8,#c9b89a)"></div>
  <div class="meta"><b>Dec 03</b><i>&#9633;0</i></div>
  <h4>Neque porro quisquam dolorem</h4>
  <p>It has survived not only five centuries, but also the leap into electronic typesetting,</p>
  <a>Read More &raquo;</a>
</div>
<div class="abs post" style="left:443px">
  <div class="img" role="img" aria-label="Glass sliding doors" style="background:linear-gradient(160deg,#dfe5e8,#9aa6ad)"></div>
  <div class="meta"><b>Dec 03</b><i>&#9633;0</i></div>
  <h4>Porro quisquam est qui</h4>
  <p>It has survived not only five centuries, but also the leap into electronic typesetting,</p>
  <a>Read More &raquo;</a>
</div>
<div class="abs post" style="left:796px">
  <div class="img" role="img" aria-label="Staircase with turquoise glass railing" style="background:linear-gradient(160deg,#7fe0ee,#2aa7bf)"></div>
  <div class="meta"><b>Dec 03</b><i>&#9633;0</i></div>
  <h4>Dolorem ipsum quia dolor</h4>
  <p>It has survived not only five centuries, but also the leap into electronic typesetting,</p>
  <a>Read More &raquo;</a>
</div>

<footer class="abs footer">
  <div class="abs brand"><div class="mark"></div><div class="name">CLEARVALE</div></div>
  <div class="abs fcol" style="left:424px">
    <h5>INFORMATION</h5>
    <div>&rsaquo; Privacy Policy</div>
    <div>&rsaquo; Your Account</div>
    <div>&rsaquo; Advanced Search</div>
    <div>&rsaquo; Contact Us</div>
  </div>
  <div class="abs fcol" style="left:654px">
    <h5>CONTACT US</h5>
    <div>Address : Harlow Yard, Mill Lane<br>Westbury, Canada</div>
    <div>Phone : 05550198274</div>
    <div>Email : info@clearvale-glass.com</div>
  </div>
  <div class="abs fcol" style="left:943px;top:66px">
    <h5>FOLLOW US OUT THERE</h5>
    <div class="fsocial"><i></i><i></i><i></i><i></i></div>
  </div>
  <div class="abs rule"></div>
  <div class="abs copy">Copyright &copy; 2018. All Rights Reserved</div>
</footer>

</body>
</html>
```